Intelligent design image for our website

I would like an awesome image for our website that showcases the intelligent design of our app. We currently have a test web site here.
https://www.corvinta.com.au/test-ewd/
I really do not like the graphic next to the "Intelligent design" and i want something much better than this.
Our app is used by Australian Truck Drivers. It would be nice to have a little bit of an Australian feel, but most importantly is should clearly showcase our app look a feel and the screens should be as legible (readable) as possible. These examples could be used for inspiration.
https://pixelmarrow.net/products/free-app-showcase-mockup-psd-5170284
https://www.plonkit.com/community/file/2640519873320957716/PhoneSuite-Landing-Page-Template-for-Mobile-Apps-Showcase

```html
<!DOCTYPE html>
<html lang="en">
<head>
<meta charset="utf-8">
<title>Intelligent design – driver activity screen</title>
<link rel="stylesheet" href="https://fonts.googleapis.com/css2?family=Lato:wght@400;700&family=Quicksand:wght@500;700&display=swap">
<style>
  :root {
    --page-bg: #fafbfa;
    --brand-green: #04a90e;
    --ink: #1d1d1f;
    --ink-soft: #5f6368;
    --muted: #b3b6ba;
    --rule: #dcdfe3;
    --accent-blue: #3aa0dc;
    --sync-blue: #2ea7f0;
    --rest-bg: #fce7e7;
    --rest-red: #e2574c;
    --screen-bg: #ffffff;
    --button-dark: #1b1b1b;
  }
  * { box-sizing: border-box; margin: 0; padding: 0; }
  html, body { width: 1156px; height: 1200px; overflow: hidden; }
  body {
    background: var(--page-bg);
    font-family: "Lato", Arial, sans-serif;
    color: var(--ink);
    position: relative;
  }
  .backdrop { position: absolute; inset: 0; }
  .app-screen {
    position: absolute;
    left: 598px; top: 104px;
    width: 392px; height: 916px;
    background: var(--screen-bg);
    border-radius: 34px;
    box-shadow: 0 18px 50px rgba(0,0,0,.12);
    overflow: hidden;
  }
  .status-bar {
    height: 50px; padding: 0 22px;
    display: flex; align-items: center; justify-content: space-between;
    font-size: 15px; font-weight: 700;
  }
  .status-icons { display: flex; gap: 5px; align-items: center; }
  .driver-header {
    position: relative;
    padding: 6px 16px 14px 16px;
    display: flex; gap: 22px;
    border-bottom: 1px solid var(--rule);
  }
  .menu-icon { margin-top: 26px; }
  .driver-name { font-family: "Quicksand", sans-serif; font-size: 20px; font-weight: 700; margin-bottom: 4px; }
  .driver-meta { font-family: "Quicksand", sans-serif; font-size: 16px; color: var(--ink-soft); line-height: 1.3; font-weight: 500; }
  .sync { position: absolute; right: 10px; top: -12px; display: flex; flex-direction: column; align-items: center; gap: 8px; }
  .sync-button {
    background: var(--sync-blue); color: #fff; font-size: 12px; font-weight: 700;
    border-radius: 8px; padding: 5px 7px;
  }
  .field {
    margin: 0 14px; padding: 20px 0 8px;
    border-bottom: 1px solid var(--rule);
    display: flex; justify-content: space-between; align-items: center;
  }
  .field-label { font-size: 13px; color: var(--ink); margin-bottom: 10px; }
  .field-value { font-size: 17px; font-weight: 700; }
  .field-placeholder { font-size: 16px; color: var(--muted); }
  .field.note { height: 118px; align-items: flex-start; }
  .char-count { text-align: right; margin: 10px 14px 0; font-size: 13px; color: var(--muted); }
  .status-panel {
    margin: 22px 14px 0; background: var(--rest-bg);
    border-radius: 10px 10px 0 0; padding: 16px 14px 8px;
  }
  .status-title {
    display: flex; justify-content: center; align-items: center; gap: 18px;
    color: var(--rest-red); font-size: 24px; font-weight: 700;
    padding-bottom: 14px; border-bottom: 1px solid #f3d3d3;
  }
  .status-options { display: flex; justify-content: space-between; padding: 12px 14px 0 6px; font-size: 16px; font-weight: 700; }
  .option { display: flex; align-items: center; gap: 8px; }
  .radio { width: 20px; height: 20px; border: 2px solid var(--ink); border-radius: 50%; display: grid; place-items: center; }
  .radio.selected::after { content: ""; width: 10px; height: 10px; border-radius: 50%; background: var(--ink); }
  .actions { display: flex; gap: 20px; margin: 10px 14px 0; }
  .btn { flex: 1; height: 48px; border-radius: 8px; display: grid; place-items: center; font-size: 16px; font-weight: 700; }
  .btn-cancel { border: 1.5px solid var(--ink); background: #fff; }
  .btn-update { background: var(--button-dark); color: #fff; }
</style>
</head>
<body>
  <svg class="backdrop" width="1156" height="1200" viewBox="0 0 1156 1200" aria-hidden="true">
    <circle cx="858" cy="560" r="336" fill="var(--brand-green)"/>
    <circle cx="858" cy="560" r="302" fill="none" stroke="#fff" stroke-width="5" stroke-linecap="round" stroke-dasharray="0 12"/>
  </svg>

  <main class="app-screen">
    <div class="status-bar">
      <span>9:41</span>
      <span class="status-icons">
        <svg width="18" height="12" viewBox="0 0 18 12"><rect x="0" y="8" width="3" height="4" fill="#111"/><rect x="5" y="5" width="3" height="7" fill="#111"/><rect x="10" y="2" width="3" height="10" fill="#111"/><rect x="15" y="0" width="3" height="12" fill="#111"/></svg>
        <svg width="16" height="12" viewBox="0 0 16 12"><path d="M1 4a10 10 0 0 1 14 0M3.5 6.5a6.5 6.5 0 0 1 9 0M6 9a3 3 0 0 1 4 0" stroke="#111" stroke-width="1.8" fill="none"/></svg>
        <svg width="24" height="12" viewBox="0 0 24 12"><rect x="0" y="1" width="22" height="10" rx="2.5" fill="#111"/></svg>
      </span>
    </div>

    <header class="driver-header">
      <svg class="menu-icon" width="22" height="18" viewBox="0 0 22 18"><path d="M1 2h16M1 9h20M7 16h14" stroke="#111" stroke-width="2.4" stroke-linecap="round"/></svg>
      <div>
        <div class="driver-name">Ned Harlow</div>
        <div class="driver-meta">License : 12345678</div>
        <div class="driver-meta">Work Option : Standard Solo</div>
      </div>
      <div class="sync">
        <svg width="26" height="20" viewBox="0 0 26 20"><path d="M7 17h13a5 5 0 0 0 0-10 7 7 0 0 0-13-1 5.5 5.5 0 0 0 0 11z" fill="none" stroke="var(--brand-green)" stroke-width="2"/><path d="M9 11l3 3 6-6" fill="none" stroke="var(--brand-green)" stroke-width="2"/></svg>
        <span class="sync-button">Sync Now</span>
      </div>
    </header>

    <section class="field">
      <div><div class="field-label">Activity Start Time (Local, UTC +08:00 AWST)</div><div class="field-value">14:09</div></div>
      <svg width="22" height="22" viewBox="0 0 22 22"><circle cx="11" cy="11" r="9" fill="none" stroke="var(--accent-blue)" stroke-width="2"/><path d="M11 6v5l3 3" fill="none" stroke="var(--accent-blue)" stroke-width="2"/></svg>
    </section>
    <section class="field">
      <div><div class="field-label">Activity Start Date</div><div class="field-value">21 Apr 2021</div></div>
      <svg width="22" height="22" viewBox="0 0 22 22"><rect x="2" y="4" width="18" height="16" rx="2" fill="none" stroke="var(--accent-blue)" stroke-width="2"/><path d="M2 9h18M7 2v4M15 2v4M7 12v6M11 12v6M15 12v6" stroke="var(--accent-blue)" stroke-width="1.5"/></svg>
    </section>
    <section class="field">
      <div><div class="field-label">Start Place</div><div class="field-value">Swanbourne</div></div>
      <svg width="22" height="22" viewBox="0 0 22 22"><circle cx="11" cy="11" r="7" fill="none" stroke="var(--accent-blue)" stroke-width="2"/><circle cx="11" cy="11" r="2.5" fill="var(--accent-blue)"/><path d="M11 1v3M11 18v3M1 11h3M18 11h3" stroke="var(--accent-blue)" stroke-width="2"/></svg>
    </section>
    <section class="field">
      <div><div class="field-label">Odometer (km)</div><div class="field-value">12345</div></div>
      <svg width="24" height="22" viewBox="0 0 24 22"><path d="M7 2a5 5 0 0 0-5 5c0 4 5 9 5 9s5-5 5-9a5 5 0 0 0-5-5z" fill="none" stroke="var(--accent-blue)" stroke-width="1.8"/><path d="M18 9a4 4 0 0 0-4 4c0 3 4 7 4 7s4-4 4-7a4 4 0 0 0-4-4z" fill="none" stroke="var(--accent-blue)" stroke-width="1.8"/><circle cx="18" cy="13" r="1.4" fill="var(--accent-blue)"/><path d="M8 17c3 0 3-3 6-3" fill="none" stroke="var(--accent-blue)" stroke-width="1.5"/></svg>
    </section>
    <section class="field">
      <div><div class="field-label">Vehicle Registration</div><div class="field-value">123ABC</div></div>
    </section>
    <section class="field note">
      <div><div class="field-label">Note</div><div class="field-placeholder">Enter note</div></div>
    </section>
    <div class="char-count">0/140</div>

    <section class="status-panel">
      <div class="status-title">
        <svg width="42" height="30" viewBox="0 0 42 30"><path d="M2 2v26M2 20h38v8M2 14h38v6" fill="none" stroke="var(--rest-red)" stroke-width="2"/><circle cx="9" cy="10" r="3.5" fill="none" stroke="var(--rest-red)" stroke-width="2"/><path d="M15 14V8h20a5 5 0 0 1 5 5v1" fill="none" stroke="var(--rest-red)" stroke-width="2"/></svg>
        <span>Resting</span>
      </div>
      <div class="status-options">
        <span class="option"><span class="radio"></span>Maintain Rest</span>
        <span class="option"><span class="radio selected"></span>Change To Work</span>
      </div>
    </section>

    <div class="actions">
      <span class="btn btn-cancel">Cancel</span>
      <span class="btn btn-update">Update</span>
    </div>
  </main>
</body>
</html>
```